Billiards 50th Anniversary Calendar

Need a custom calendar designed to finish at 8.5 x 11. and to be supplied as a pdf print file including .25 bleed on all sides. Total is 24 pages. I will supply one image per calendar month. Cover to have a collage of monthly images or samples of some of your favorites incorporated with a cool design that transitions throughout the calendar. The client's 50th Anniversary logo must be incorporated into the design.

Back cover has a group image to be incorporated as well.

Target Market(s)

Calendar is selling to their billiard clients

Industry/Entity Type

Male dominant industry

Requirements
Must have
• Must have a design element that continues through the calendar but flows with the images well. One image per calendar month.

```html
<!DOCTYPE html>
<html lang="en">
<head>
<meta charset="utf-8">
<title>Cueworks Billiards 2022 Calendar Cover</title>
<link href="https://fonts.googleapis.com/css2?family=Archivo+Black&display=swap" rel="stylesheet">
<style>
  :root {
    --backdrop: #d9d4cc;
    --cover-black: #000000;
    --tile-grey: #333333;
    --accent-orange: #ef861d;
    --text-white: #ffffff;
    --photo-light: #8a8a8a;
    --photo-dark: #1e1e1e;
  }
  * { margin: 0; padding: 0; box-sizing: border-box; }
  html, body {
    width: 1200px;
    height: 971px;
    overflow: hidden;
    background: var(--backdrop);
  }
  .cover {
    position: absolute;
    left: 20px;
    top: 37px;
    width: 1160px;
    height: 896px;
    background: var(--cover-black);
    font-family: "Archivo Black", "Arial Black", sans-serif;
  }
  .brand {
    position: absolute;
    left: 930px;
    top: 92px;
    width: 170px;
    display: flex;
    align-items: center;
    gap: 10px;
    color: var(--accent-orange);
    font-size: 21px;
    line-height: 1.1;
    text-transform: uppercase;
  }
  .brand-dot {
    flex: none;
    width: 26px;
    height: 26px;
    border-radius: 50%;
    background: var(--accent-orange);
  }
  .title {
    position: absolute;
    left: 309px;
    top: 245px;
    width: 542px;
  }
  .title-year {
    display: block;
    color: var(--accent-orange);
    font-size: 214px;
    line-height: 1;
    letter-spacing: -6px;
    text-align: center;
  }
  .title-word {
    display: flex;
    justify-content: space-between;
    margin-top: 4px;
    padding: 0 2px;
    color: var(--text-white);
    font-size: 21px;
    line-height: 1;
  }
  .month-grid {
    position: absolute;
    left: 0;
    top: 599px;
    width: 1160px;
    height: 297px;
    display: grid;
    grid-template-columns: repeat(7, 1fr);
    grid-template-rows: repeat(2, 1fr);
  }
  .tile { background: var(--tile-grey); }
  .tile-photo {
    background: radial-gradient(ellipse at 50% 45%, var(--photo-light) 0%, #4a4a4a 45%, var(--photo-dark) 100%);
  }
</style>
</head>
<body>
  <main class="cover">
    <div class="brand">
      <span class="brand-dot"></span>
      <span class="brand-name">Cueworks<br>Billiards</span>
    </div>

    <h1 class="title">
      <span class="title-year">2022</span>
      <span class="title-word"><span>C</span><span>A</span><span>L</span><span>E</span><span>N</span><span>D</span><span>E</span><span>R</span></span>
    </h1>

    <section class="month-grid">
      <div class="tile tile-photo" role="img" aria-label="Black and white photo of a model in a flapper headband seated at a pool table"></div>
      <div class="tile"></div>
      <div class="tile tile-photo" role="img" aria-label="Black and white photo of a model with a flower in her hair holding a cue ball"></div>
      <div class="tile"></div>
      <div class="tile tile-photo" role="img" aria-label="Black and white photo of a model lying on a pool table with a finger to her lips"></div>
      <div class="tile"></div>
      <div class="tile tile-photo" role="img" aria-label="Black and white photo of a model sitting on a pool table holding a cue"></div>

      <div class="tile"></div>
      <div class="tile tile-photo" role="img" aria-label="Black and white photo of a smiling model leaning on a pool table with balls and a cue"></div>
      <div class="tile"></div>
      <div class="tile tile-photo" role="img" aria-label="Black and white photo of a model in a leopard print dress by a pool table"></div>
      <div class="tile"></div>
      <div class="tile tile-photo" role="img" aria-label="Black and white photo of a pin-up model in a polka dot dress lying on a pool table"></div>
      <div class="tile"></div>
    </section>
  </main>
</body>
</html>
```